ecommerce news podcast artwork

Podcast cover art for a podcast featuring daily news and events around ecommerce product businesses.

text to be: BRISK LOOP
optional third line of text with smaller font: Podcast

looking for something that pops with a medium to light blue background. text can be in white/red/orange colors. prefer solid colors for text, but background can vary.
I'm really open to other ideas too, sometimes you don't know what you want until you see it.

Target Market(s)

ecommerce business owners, managers

Industry/Entity Type

news, business, ecommerce

Font styles to use
Sans Serif

Colors
0054AA
0677BA
7BADD7
CADEEF
E8F1F8
0094D4
00A9DD
6FCCEA
C7EBF8
E9F6FB
F0912C
F2A743
F7CA91
FBE8D2
FDF5EE
EB3D1F
EC4F4E
F09395
F8D3D4
FCEDEE

Requirements
Must have
• text: BRISK LOOP
Should not have
• no microphones, headsets/headphones, speakers, or other props like that.

```html
<!DOCTYPE html>
<html lang="en">
<head>
<meta charset="utf-8">
<title>Brisk Loop Podcast Cover</title>
<link rel="stylesheet" href="https://fonts.googleapis.com/css2?family=League+Spartan:wght@600;700&display=swap">
<style>
  :root {
    --cover-bg: #2a0858;
    --title-cyan: #22cfe8;
    --title-white: #ffffff;
    --glow-magenta: #a31fc4;
    --glow-violet: #5b1aa8;
    --glow-deep: #2a0858;
  }
  html, body {
    margin: 0;
    padding: 0;
    width: 1200px;
    height: 1200px;
    overflow: hidden;
    background: var(--cover-bg);
  }
  .cover {
    position: relative;
    width: 1200px;
    height: 1200px;
    background: var(--cover-bg);
    font-family: "League Spartan", "Helvetica Neue", Arial, sans-serif;
    overflow: hidden;
  }
  .shop-illustration {
    position: absolute;
    left: 420px;
    top: 500px;
    width: 730px;
    height: 650px;
    background: radial-gradient(ellipse at 55% 60%, var(--glow-magenta) 0%, var(--glow-violet) 38%, var(--glow-deep) 72%);
    border-radius: 40%;
  }
  .title {
    position: absolute;
    left: 108px;
    margin: 0;
    font-weight: 700;
    line-height: 1;
    white-space: nowrap;
  }
  .title-top {
    top: 104px;
    font-size: 252px;
    color: var(--title-cyan);
    letter-spacing: 2px;
  }
  .title-bottom {
    top: 296px;
    font-size: 405px;
    color: var(--title-white);
    letter-spacing: -4px;
  }
  .show-label {
    position: absolute;
    left: 114px;
    top: 1030px;
    margin: 0;
    font-size: 52px;
    font-weight: 600;
    line-height: 1;
    letter-spacing: 17px;
    color: var(--title-white);
  }
</style>
</head>
<body>
  <main class="cover">
    <div class="shop-illustration" role="img" aria-label="Isometric illustration of a shopping cart with bags on a smartphone, with a buy button, coins, a receipt and a credit card"></div>
    <h1 class="title title-top">BRISK</h1>
    <p class="title title-bottom">LOOP</p>
    <p class="show-label">PODCAST</p>
  </main>
</body>
</html>
```